Indy Film Production Company/Studio

We need a business card designed from an existing logo. We are a digital studio/production company that caters to creating genre entertainment, like Action, Horror, and martial arts. The card along with the logo will be used to Brand the company from letter heads to banners. The design will also be used for postcards and Brochures. It should be professional and masculine.
Updates

Thank you to all the designers who have participated. I'm narrowing down who it will be. Thank you again.

Target Market(s)

Investors, Networks, Producers, and actors

Industry/Entity Type

Film Production

Contact Information for Business Card

Teodoro Valbuena
Producer/Writer/Director
www.kestrelpicturehouse.example

Requirements
Must have
• Website address, Facebook icon and Twitter icon possibly in the back of the card.
Nice to have
• Logline of Company: Follow The Action.

```html
<!DOCTYPE html>
<html lang="en">
<head>
<meta charset="utf-8">
<title>Kestrel Picture House – Business Card</title>
<link rel="stylesheet" href="https://fonts.googleapis.com/css2?family=Open+Sans:wght@400;600;800&display=swap">
<style>
  :root {
    --page: #2b2623;
    --card: #111111;
    --card-edge: #1c1c1c;
    --white: #f2f2f2;
    --grey: #bdbdbd;
    --red: #e0232b;
    --photo-dark: #0c0c0c;
    --photo-mid: #3a3a3a;
  }
  * { margin: 0; padding: 0; box-sizing: border-box; }
  html, body { width: 1200px; height: 814px; overflow: hidden; background: var(--page); }
  body { position: relative; font-family: "Open Sans", Arial, sans-serif; color: var(--white); }

  .card {
    position: absolute;
    width: 520px; height: 298px;
    background: var(--card);
    border: 1px solid var(--card-edge);
    box-shadow: 0 10px 28px rgba(0,0,0,.45);
    overflow: hidden;
  }
  .card--front { left: 50px; top: 258px; }
  .card--back  { left: 630px; top: 258px; }

  /* front */
  .camera-photo {
    position: absolute; left: 0; top: 18px;
    width: 270px; height: 280px;
    background: radial-gradient(ellipse at 45% 45%, var(--photo-mid) 0%, #222 40%, var(--photo-dark) 75%, transparent 100%);
  }
  .contact {
    position: absolute; right: 26px; top: 58px;
    text-align: right;
  }
  .brand-name {
    font-weight: 800; font-size: 21px; letter-spacing: .5px;
    text-transform: uppercase; color: var(--white);
    line-height: 1.1; margin-bottom: 8px;
  }
  .person-name { color: var(--red); font-size: 19px; font-weight: 600; line-height: 1.2; }
  .person-role { font-size: 15px; color: var(--white); margin-bottom: 6px; }
  .contact-line {
    display: flex; justify-content: flex-end; align-items: center; gap: 8px;
    font-size: 13px; color: var(--white); line-height: 1.75;
  }
  .contact-line svg { width: 12px; height: 12px; fill: var(--red); flex: none; }

  /* back */
  .social {
    position: absolute; right: 18px; top: 14px;
    display: flex; gap: 5px;
  }
  .social span { width: 13px; height: 13px; border-radius: 50%; background: #3a3a3a; }
  .back-brand {
    position: absolute; left: 0; right: 0; top: 112px;
    text-align: center;
  }
  .back-brand .brand-name { font-size: 28px; margin-bottom: 6px; }
  .back-web { font-size: 13px; letter-spacing: 2.5px; color: var(--grey); }
</style>
</head>
<body>

<section class="card card--front" aria-label="Business card front">
  <div class="camera-photo" role="img" aria-label="Photo of a rigged digital cinema camera on a tripod head"></div>
  <div class="contact">
    <p class="brand-name">Kestrel Picture House</p>
    <p class="person-name">Teodoro Valbuena</p>
    <p class="person-role">Producer/Writer/Director</p>
    <p class="contact-line">555 014 2290
      <svg viewBox="0 0 24 24" aria-hidden="true"><path d="M6.6 10.8a15.1 15.1 0 0 0 6.6 6.6l2.2-2.2c.3-.3.7-.4 1-.2 1.1.4 2.3.6 3.6.6.6 0 1 .4 1 1V20c0 .6-.4 1-1 1A17 17 0 0 1 3 4c0-.6.4-1 1-1h3.5c.6 0 1 .4 1 1 0 1.3.2 2.5.6 3.6.1.3 0 .7-.2 1z"/></svg>
    </p>
    <p class="contact-line">name@kestrelpicturehouse.example
      <svg viewBox="0 0 24 24" aria-hidden="true"><path d="M2 5h20v14H2z M4 7v.5l8 5 8-5V7l-8 5z" fill-rule="evenodd"/></svg>
    </p>
    <p class="contact-line">www.kestrelpicturehouse.example
      <svg viewBox="0 0 24 24" aria-hidden="true"><circle cx="12" cy="12" r="10"/><path d="M2 12h20M12 2c3 3 3 17 0 20M12 2c-3 3-3 17 0 20" stroke="#111" stroke-width="1.6" fill="none"/></svg>
    </p>
  </div>
</section>

<section class="card card--back" aria-label="Business card back">
  <div class="social" aria-label="Social links"><span></span><span></span><span></span></div>
  <div class="back-brand">
    <p class="brand-name">Kestrel Picture House</p>
    <p class="back-web">www.kestrelpicturehouse.example</p>
  </div>
</section>

</body>
</html>
```